Business Card Design for Software Development Company

I am looking for a business card design the incorporates my new logo (attached below).

Key information to include:
Name: Martin Quelbrook
Title: CEO
Email: martin@brightwellcivic.example
Phone: 555-218-9403
Website: www.brightwellcivic.example

NOTE: This design should be easy to edit so that we can order cards for different members of our team.

```html
<!DOCTYPE html>
<html lang="en">
<head>
<meta charset="utf-8">
<title>Brightwell Labs – Business Card</title>
<link href="https://fonts.googleapis.com/css2?family=Montserrat:wght@400;600;700&display=swap" rel="stylesheet">
<style>
  :root{
    --stage:#171717;
    --card-light:#f4f4f4;
    --card-dark:#1f1f1f;
    --ink:#222222;
    --ink-soft:#2e2e2e;
    --teal:#1aa597;
    --orange:#e87a24;
    --mark-dark:#8a8a8a;
    --tag-dark:#2c2c2c;
  }
  *{margin:0;padding:0;box-sizing:border-box}
  html,body{width:1200px;height:1059px;overflow:hidden}
  body{background:var(--stage);font-family:"Montserrat",Arial,sans-serif;position:relative}

  .card{position:absolute;left:255px;width:690px;height:390px;border-radius:18px}
  .card--front{top:89px;background:var(--card-light)}
  .card--back{top:547px;background:var(--card-dark)}

  .brand{position:absolute;left:0;right:0;display:flex;flex-direction:column;align-items:center}
  .brand__row{display:flex;align-items:center;gap:12px}
  .brand__dot{width:22px;height:22px;border-radius:50%;background:var(--teal)}
  .brand__name{font-weight:700;letter-spacing:-1px;line-height:1}
  .brand__tag{font-weight:600;text-transform:uppercase;letter-spacing:.3px;align-self:flex-end}

  .card--front .brand{top:80px}
  .card--front .brand__name{font-size:44px;color:var(--ink)}
  .card--front .brand__tag{font-size:6px;color:var(--ink);margin-right:172px;margin-top:4px}

  .card--back .brand{top:160px}
  .card--back .brand__dot{width:28px;height:28px}
  .card--back .brand__name{font-size:58px;color:var(--mark-dark)}
  .card--back .brand__tag{font-size:8px;color:var(--tag-dark);margin-right:126px;margin-top:5px}

  .person{position:absolute;right:373px;top:252px;text-align:right}
  .person__name{font-size:22px;font-weight:700;letter-spacing:.2px;white-space:nowrap}
  .person__first{color:var(--teal)}
  .person__last{color:var(--orange)}
  .person__title{font-size:17px;color:var(--ink-soft);margin-top:4px}

  .divider{position:absolute;left:343px;top:236px;width:1.5px;height:80px;background:var(--teal)}

  .contact{position:absolute;left:371px;top:231px;list-style:none}
  .contact__item{display:flex;align-items:center;gap:8px;height:31.5px;font-size:16.5px;color:var(--ink)}
  .contact__icon{width:14px;height:14px;flex:none}
</style>
</head>
<body>

<section class="card card--front">
  <div class="brand">
    <div class="brand__row">
      <span class="brand__dot"></span>
      <span class="brand__name">Brightwell Labs</span>
    </div>
    <span class="brand__tag">A division of Brightwell Civic</span>
  </div>

  <div class="person">
    <p class="person__name"><span class="person__first">MARTIN</span> <span class="person__last">QUELBROOK</span></p>
    <p class="person__title">CEO</p>
  </div>

  <span class="divider"></span>

  <ul class="contact">
    <li class="contact__item">
      <svg class="contact__icon" viewBox="0 0 16 16"><path fill="#f0a868" d="M1 6c0-2 3-4 7-4s7 2 7 4v1h-4V5.5H5V7H1zM4 8h8l2 6H2z"/></svg>
      555-218-9403
    </li>
    <li class="contact__item">
      <svg class="contact__icon" viewBox="0 0 16 16"><path fill="var(--teal)" d="M1 6l7-5 7 5v9H1zm2 1v6h10V7l-5 3.5z"/></svg>
      martin@brightwellcivic.example
    </li>
    <li class="contact__item">
      <svg class="contact__icon" viewBox="0 0 16 16"><circle cx="8" cy="8" r="7" fill="var(--orange)"/><path fill="#f6c193" d="M4 4c2 0 3 1 2 3s1 3-1 5C3 10 2 7 4 4zm6 1c2 0 3 3 2 5-1 0-2-1-2-3z"/></svg>
      www.brightwellcivic.example
    </li>
  </ul>
</section>

<section class="card card--back">
  <div class="brand">
    <div class="brand__row">
      <span class="brand__dot"></span>
      <span class="brand__name">Brightwell Labs</span>
    </div>
    <span class="brand__tag">A division of Brightwell Civic</span>
  </div>
</section>

</body>
</html>
```